Business card for marketing analytics company

Need a business card for new company. I have a logo already that I want to be built into the card and should use those colours

Company is called steered by tallies
Design must bring steered by tallies to life not be a card that could be for anyone with a logo put on it.

Like the front to be fairly clean and uncluttered bringing the logo out with a suitable design on the back of the card.

The logo represents a compass and business growth so those themes along with numbers, analytics , data are appropriate.
I'm often working with creative industries so also needs to reflect the creative side of analytics rather than be very corporate looking.

Target Market(s)

Ad agency, media agency, consumer goods clients

Industry/Entity Type

Market Research

Contact Information for Business Card

Needs to include name, title, email and phone number

Colors
f78f20
f68d4d
ec1f27

Requirements
Must have
• Must bring steered by tallies to life not be a card that could be for anyone with a logo put on it.
• Logo, Correct colours
• Like a design on the back that relates to company name
• Designs for both sides
Should not have
• Please do not just submit logo and a coloured card.
• It needs to have a design element to it
• No black background
• No clear cards - needs front & back

```html
<!DOCTYPE html>
<html lang="en">
<head>
<meta charset="utf-8">
<title>Steered by Tallies – Business Card</title>
<link href="https://fonts.googleapis.com/css2?family=Montserrat:wght@600&family=Work+Sans:wght@400;500;600&display=swap" rel="stylesheet">
<style>
  :root {
    --backdrop: #e9e7e4;
    --card: #ffffff;
    --card-edge: #d9d6d2;
    --brand-orange: #f78f20;
    --brand-peach: #f68d4d;
    --brand-red: #ec1f27;
    --text-dark: #2b2b2d;
    --text-mid: #55565a;
    --divider: #c9c6c2;
  }
  * { margin: 0; padding: 0; box-sizing: border-box; }
  html, body {
    width: 1200px;
    height: 1000px;
    overflow: hidden;
    background: var(--backdrop);
  }
  .canvas {
    position: relative;
    width: 1200px;
    height: 1000px;
  }
  .card {
    position: absolute;
    left: 240px;
    width: 720px;
    height: 410px;
    background: var(--card);
    overflow: hidden;
    box-shadow: 0 14px 34px rgba(0,0,0,0.14), 0 0 0 1px var(--card-edge);
  }
  .card--front { top: 50px; }
  .card--back { top: 530px; }

  .edge-band {
    position: absolute;
    left: 0;
    bottom: 0;
    width: 100%;
    height: 14px;
    background: linear-gradient(90deg, var(--brand-orange), var(--brand-peach) 55%, var(--brand-red));
  }

  /* Front */
  .brand {
    position: absolute;
    left: 150px;
    top: 130px;
    display: flex;
    align-items: center;
    gap: 34px;
  }
  .brand__dot {
    width: 130px;
    height: 130px;
    border-radius: 50%;
    border: 4px solid var(--brand-orange);
    flex: none;
  }
  .brand__name {
    font-family: "Work Sans", sans-serif;
    font-weight: 600;
    font-size: 42px;
    line-height: 1.05;
    letter-spacing: 1px;
    color: var(--text-dark);
  }
  .brand__name span { display: block; }
  .brand__name span + span { padding-left: 56px; }

  /* Back */
  .growth-chart {
    position: absolute;
    right: 40px;
    top: 34px;
    width: 150px;
    height: 84px;
  }
  .identity {
    position: absolute;
    right: 400px;
    top: 150px;
    text-align: right;
  }
  .identity__name {
    font-family: "Montserrat", sans-serif;
    font-weight: 600;
    font-size: 31px;
    letter-spacing: 1px;
    color: var(--brand-red);
    white-space: nowrap;
  }
  .identity__title {
    margin-top: 6px;
    font-family: "Montserrat", sans-serif;
    font-weight: 600;
    font-size: 17px;
    letter-spacing: 1px;
    color: var(--text-dark);
  }
  .divider {
    position: absolute;
    left: 336px;
    top: 140px;
    width: 2px;
    height: 92px;
    background: var(--divider);
  }
  .contacts {
    position: absolute;
    left: 360px;
    top: 150px;
    list-style: none;
    font-family: "Work Sans", sans-serif;
    font-size: 19px;
    color: var(--text-dark);
    letter-spacing: 1px;
  }
  .contacts li {
    display: flex;
    align-items: center;
    gap: 14px;
    height: 27px;
  }
  .contacts svg { width: 18px; height: 18px; flex: none; }
  .contacts .highlight { color: var(--brand-red); }
  .address {
    position: absolute;
    left: 130px;
    top: 322px;
    display: flex;
    align-items: center;
    gap: 18px;
    font-family: "Work Sans", sans-serif;
    font-size: 19px;
    letter-spacing: 1px;
    color: var(--text-mid);
  }
  .address svg { width: 18px; height: 18px; }
</style>
</head>
<body>
<main class="canvas">
  <section class="card card--front" aria-label="Card front">
    <div class="brand">
      <div class="brand__dot"></div>
      <div class="brand__name"><span>Steered by</span><span>Tallies</span></div>
    </div>
    <div class="edge-band"></div>
  </section>

  <section class="card card--back" aria-label="Card back">
    <svg class="growth-chart" viewBox="0 0 150 84" aria-hidden="true">
      <rect x="0" y="60" width="18" height="24" fill="#f78f20"/>
      <rect x="26" y="48" width="18" height="36" fill="#f78f20"/>
      <rect x="52" y="52" width="18" height="32" fill="#f68d4d"/>
      <rect x="78" y="34" width="18" height="50" fill="#f68d4d"/>
      <rect x="104" y="20" width="18" height="64" fill="#ec1f27"/>
      <rect x="130" y="4" width="18" height="80" fill="#ec1f27"/>
    </svg>
    <div class="identity">
      <div class="identity__name">DANIEL PARKER</div>
      <div class="identity__title">FOUNDER</div>
    </div>
    <div class="divider"></div>
    <ul class="contacts">
      <li>
        <svg viewBox="0 0 20 20" aria-hidden="true"><path fill="#ec1f27" d="M5 2h3l1.5 4-2 1.5a11 11 0 0 0 5 5L14 10.5l4 1.5v3a2 2 0 0 1-2 2A14 14 0 0 1 3 4a2 2 0 0 1 2-2z"/></svg>
        <span>000 000 0000</span>
      </li>
      <li>
        <svg viewBox="0 0 20 20" aria-hidden="true"><rect x="2" y="4" width="16" height="12" rx="1" fill="#ec1f27"/><path d="M2.5 5l7.5 6 7.5-6" fill="none" stroke="#ffffff" stroke-width="1.6"/></svg>
        <span>info@yourmail.com</span>
      </li>
      <li>
        <svg viewBox="0 0 20 20" aria-hidden="true"><circle cx="12" cy="8" r="5" fill="none" stroke="#ec1f27" stroke-width="2.4"/><path d="M8.5 11.5L3 17" stroke="#ec1f27" stroke-width="3" stroke-linecap="round"/></svg>
        <span>www.<span class="highlight">yoursite</span>.com</span>
      </li>
    </ul>
    <div class="address">
      <svg viewBox="0 0 20 20" aria-hidden="true"><path fill="#f78f20" d="M18 2L2 9l7 2 2 7z"/></svg>
      <span>your street address, suite-123, country-1230</span>
    </div>
    <div class="edge-band"></div>
  </section>
</main>
</body>
</html>
```